Business Cards for new orthopaedic surgery practice

My husband and I are starting our own orthopaedic surgery practice. We are looking for a business card that is uniform, but one will have my name/title and the other will have his. You can just create one design with my name on it for now. But when I choose your design as the winning design I will ask that you add another copy with his name/title.

We are looking for classy, simple, elite all in one. We like dark blues/a little gold/yellow. Something that goes with our logo. We want our logo incorporated. Here is all the info you need:
Business name: RV Bone & Vitality Center
Location: 38517 North Willowmere Ave
Maple Hollow, FL 34290
Phone: 954-218-4063
Fax: 954-582-7341
Email: info@myrvbonecare.example

Names: Lydia Vance, M.D.
Board Certified Hand and Upper Extremity Surgeon

Ebo Dansu, M.D.
Board Certified Hip & Knee Replacement/General Orthopaedic Surgeon

Can decide what you want to put on the back. Maybe a slogan:
Grounded in Care. Centered on You

I am just going to upload our logo. The only thing is if we select you as the winning design, the location, and phone numbers may change. We will need your help to update that once fully solidified.

Industry/Entity Type

Medical

Contact Information for Business Card

Colors
0054AA
0677BA
7BADD7
CADEEF
E8F1F8
0094D4
00A9DD
6FCCEA
C7EBF8
E9F6FB

Requirements
Must have
• class, appeal,
Should not have
• We want to air on the side of masculine if we are looking at masculine vs. feminine feel. But we still want it classy, sophisticated, and something we will love

```html
<!DOCTYPE html>
<html lang="en">
<head>
<meta charset="utf-8">
<title>RV Bone &amp; Vitality Center – Business Cards</title>
<link href="https://fonts.googleapis.com/css2?family=Crimson+Pro:wght@400;600&display=swap" rel="stylesheet">
<style>
  :root {
    --backdrop: #e4dfd2;
    --card: #f3f3f2;
    --navy: #15234d;
    --gold: #b8913f;
    --ink: #3c3f47;
    --rule: #6d7180;
    --ghost: #e0e0df;
  }
  * { margin: 0; padding: 0; box-sizing: border-box; }
  html, body { width: 1200px; height: 900px; overflow: hidden; }
  body {
    background: var(--backdrop);
    font-family: "Crimson Pro", Georgia, serif;
    color: var(--ink);
    position: relative;
  }
  .card {
    position: absolute;
    left: 320px;
    width: 560px;
    height: 320px;
    background: var(--card);
    border-bottom: 7px solid var(--navy);
    box-shadow: 0 14px 30px rgba(60, 50, 20, 0.22);
    overflow: hidden;
  }
  .card--front { top: 100px; }
  .card--back { top: 480px; }

  .ghost-mark {
    position: absolute;
    left: 28px;
    font-size: 44px;
    font-weight: 600;
    line-height: 1;
    color: var(--ghost);
    white-space: nowrap;
  }
  .card--front .ghost-mark { top: 26px; }
  .card--back .ghost-mark { bottom: 26px; }

  .brand {
    position: absolute;
    top: 26px;
    right: 34px;
    width: 150px;
    display: flex;
    flex-direction: column;
    align-items: center;
    text-align: center;
  }
  .brand__dot {
    width: 14px; height: 14px;
    border-radius: 50%;
    border: 2px solid var(--gold);
    margin-bottom: 8px;
  }
  .brand__name {
    font-size: 19px;
    font-weight: 600;
    line-height: 1.15;
    letter-spacing: 0.06em;
    text-transform: uppercase;
    color: var(--navy);
  }

  .person {
    position: absolute;
    left: 50px;
    top: 144px;
  }
  .person__name {
    font-size: 21px;
    font-weight: 600;
    letter-spacing: 0.02em;
    color: var(--navy);
    text-transform: uppercase;
    line-height: 1.05;
  }
  .person__title { font-size: 16px; line-height: 1.2; }

  .divider {
    position: absolute;
    left: 50px;
    right: 34px;
    top: 192px;
    border-top: 1px solid var(--rule);
  }

  .contacts {
    position: absolute;
    left: 50px;
    top: 206px;
    list-style: none;
    font-size: 16px;
    line-height: 1.45;
  }
  .contacts li { display: flex; align-items: center; gap: 8px; }
  .contacts svg { width: 13px; height: 13px; fill: var(--gold); flex: none; }

  .address {
    position: absolute;
    right: 34px;
    top: 212px;
    text-align: right;
    font-size: 16px;
    line-height: 1.3;
    font-style: normal;
  }

  .slogan {
    position: absolute;
    right: 34px;
    top: 200px;
    font-size: 21px;
    font-weight: 600;
    color: var(--gold);
  }
</style>
</head>
<body>

  <section class="card card--front" aria-label="Business card front">
    <div class="ghost-mark" aria-hidden="true">RV Bone &amp;<br>Vitality</div>

    <div class="brand">
      <span class="brand__dot"></span>
      <span class="brand__name">RV Bone &amp; Vitality Center</span>
    </div>

    <div class="person">
      <h1 class="person__name">Lydia Vance, M.D.</h1>
      <p class="person__title">Board Certified Hand and Upper Extremity Surgeon</p>
    </div>

    <div class="divider"></div>

    <ul class="contacts">
      <li>
        <svg viewBox="0 0 16 16" aria-label="Phone"><path d="M3.6 1.5l2.3 2.6-1.3 1.9c.9 2 2.4 3.5 4.4 4.4l1.9-1.3 2.6 2.3-1.4 2.6C6.8 13.8 2.2 9.2 1 3z"/></svg>
        954-218-4063
      </li>
      <li>
        <svg viewBox="0 0 16 16" aria-label="Fax"><path d="M4 1h7v4H4zM1 6h14v6h-3v3H4v-3H1zm4 4v4h6v-4z"/></svg>
        954-582-7341
      </li>
      <li>
        <svg viewBox="0 0 16 16" aria-label="Email"><path d="M1 3h14v10H1zm1.5 1.2L8 8.6l5.5-4.4z"/></svg>
        info@myrvbonecare.example
      </li>
    </ul>

    <address class="address">
      38517 North Willowmere Ave<br>
      Maple Hollow, FL 34290
    </address>
  </section>

  <section class="card card--back" aria-label="Business card back">
    <div class="ghost-mark" aria-hidden="true">RV Bone &amp;<br>Vitality</div>

    <div class="brand">
      <span class="brand__dot"></span>
      <span class="brand__name">RV Bone &amp; Vitality Center</span>
    </div>

    <p class="slogan">Grounded in Care. Centered on You</p>
  </section>

</body>
</html>
```